Reach Crafters Unique Marketing Website Design

I am starting a new company that is a thought leader in the marketing consulting space. The company is called Reach Crafters. We intend to build a Wordpress site on the Astra Theme with the Spectra builder. Our goal is to become the leading voice that empowers high-ticket service business leaders to become Reach Crafters by equipping them with the cutting-edge frameworks and decision grade intelligence taught in leading business schools. What we are looking for is a website design that is clean and professional, making some use of white space well also being eye catching and distinctive in the consulting space. We will probably want to have a video on the homepage not in the hero section, but just below to explain the company and what we do. Our tagline is "Be found. Be chosen." I have attached a brand guide with some messaging, our typography choices, and our color system. The full site will have a primary nav that is four pages - About us, Services, Insights (essentially a blog), and Contact Us. The goal of this project is to develop an art direction that I can give to a designer to build loads of new pages.

Target Market(s)

Business owners (mostly male) from 30-60 years old, looking to fix their sales and marketing funnel.

Industry/Entity Type

Marketing consulting

Font styles to use
Sans Serif

Requirements
Must have
• A clean, professional design that builds trust with owners of high-ticket service businesses. We need a space for explainer video, and sections that tell prospects what we do. Would also like to have a blog carousel.
Nice to have
• Social feeds, if possible. See attached documents for colors and fonts.
Should not have
• Our feel is professional enough to be trustworthy, but unique enough to be memorable. Cartoon ideas do not meet the professional test, and we do not want the website to appear feminine.

```html
<!DOCTYPE html>
<html lang="en">
<head>
<meta charset="utf-8">
<title>Reach Crafters — Be Found. Be Chosen.</title>
<link rel="stylesheet" href="https://fonts.googleapis.com/css2?family=Oswald:wght@400;500;600;700&family=Poppins:ital,wght@0,400;0,500;0,600;1,400&family=Playfair+Display:ital,wght@1,500&display=swap">
<style>
:root{
  --blue:#2f58f6;
  --blue-dark:#2447d8;
  --ink:#1d1f24;
  --text:#3c3f46;
  --muted:#7c8088;
  --line:#d9dbe0;
  --green:#1fa35c;
  --teal:#1cab8c;
  --mint:#e7f4ee;
  --footer:#232427;
  --white:#ffffff;
}
*{margin:0;padding:0;box-sizing:border-box}
html,body{width:1200px;height:4906px;overflow:hidden}
body{font-family:"Poppins",sans-serif;color:var(--text);background:var(--white);position:relative}
.abs{position:absolute}
.heading{font-family:"Oswald",sans-serif;font-weight:500;color:var(--ink);letter-spacing:.2px}
.sub{font-style:italic;font-size:13px;color:var(--text)}
.center{left:0;width:1200px;text-align:center}
.btn{position:absolute;background:var(--blue);color:var(--white);font-size:13px;display:flex;align-items:center;justify-content:center}
.photo{position:absolute}

/* Hero */
.hero{position:absolute;left:0;top:0;width:1200px;height:676px;background:linear-gradient(100deg,#1c2430 0%,#2c3644 35%,#3a4352 55%,#5a5650 80%,#4a4a4c 100%)}
.brand{position:absolute;display:flex;align-items:center;gap:10px;font-family:"Poppins",sans-serif;font-weight:600;color:var(--white)}
.brand-mark{width:14px;height:14px;background:var(--blue)}
.nav{position:absolute;top:46px;font-size:12px;color:var(--white);letter-spacing:.3px}
.social{position:absolute;width:14px;height:14px;border-radius:50%;border:2px solid currentColor}
.hero-title{position:absolute;left:160px;top:200px;font-family:"Oswald",sans-serif;font-weight:700;font-size:96px;line-height:86px;color:var(--white)}
.hero-text{position:absolute;left:162px;top:390px;width:500px;font-size:13px;line-height:17px;color:var(--white)}
.dot-ring{position:absolute;width:34px;height:34px;border-radius:50%;border:1px solid rgba(255,255,255,.6)}

/* Who we are */
.who-text{position:absolute;left:610px;top:778px;width:432px;font-size:12px;line-height:19.5px;color:var(--text)}

/* How we help */
.help-panel{position:absolute;left:0;top:1149px;width:653px;height:474px;background:var(--blue);color:var(--white)}
.step{position:absolute;left:139px;width:420px}
.step-num{position:absolute;left:0;top:0;width:42px;height:42px;border-radius:50%;background:var(--white);color:var(--ink);font-size:14px;display:flex;align-items:center;justify-content:center;box-shadow:0 0 0 5px rgba(255,255,255,.25)}
.step-title{position:absolute;left:65px;top:-2px;font-family:"Oswald",sans-serif;font-weight:500;font-size:17px;color:var(--white)}
.step-text{position:absolute;left:65px;top:24px;width:370px;font-size:11px;line-height:13px;color:var(--white)}

/* Services */
.service{position:absolute;top:1829px;width:320px}
.service-img{width:320px;height:428px}
.service-arrow{position:absolute;right:8px;top:394px}
.service-cat{position:absolute;top:455px;font-size:11px;color:var(--ink)}
.service-name{position:absolute;top:472px;font-size:15px;color:var(--ink)}
.service-line{position:absolute;top:502px;left:0;width:320px;height:2px;background:#3a3d44}

/* Testimonials */
.quote-panel{position:absolute;background:var(--mint)}
.quote-name{position:absolute;font-family:"Oswald",sans-serif;font-size:17px;color:var(--blue)}
.quote-role{position:absolute;font-size:13px;color:var(--text)}
.quote-text{position:absolute;width:475px;font-size:11px;line-height:17px;color:var(--text)}

/* Blog */
.post{position:absolute;top:3385px;width:276px}
.post-img{width:276px;height:204px}
.post-title{margin-top:14px;font-size:14px;line-height:17px;font-weight:500;color:var(--ink);height:34px}
.post-excerpt{margin-top:8px;font-size:11px;line-height:19px;color:var(--muted)}
.post-rule{margin-top:6px;height:1px;background:var(--line)}
.post-author{margin-top:8px;font-size:11px;color:var(--blue)}
.post-date{font-size:11px;color:var(--muted);letter-spacing:.5px}

/* Contact */
.contact-card{position:absolute;left:354px;top:3901px;width:492px;height:585px;background:var(--white);box-shadow:0 0 30px rgba(0,0,0,.12)}
.field{position:absolute;font-size:11px;color:var(--muted);padding-bottom:14px;border-bottom:1px solid var(--line)}
.captcha{position:absolute;left:134px;top:419px;width:226px;height:59px;border:1px solid #d3d3d3;background:#f9f9f9;border-radius:3px}

/* Footer */
.footer{position:absolute;left:0;top:4486px;width:1200px;height:420px;background:var(--footer);color:var(--white)}
.foot-head{position:absolute;font-size:13px;font-weight:500}
.foot-list{position:absolute;list-style:none;font-size:11px;line-height:30px}
.foot-small{position:absolute;font-size:11px}
.cta{position:absolute;left:790px;top:278px;font-family:"Poppins",sans-serif;font-size:58px;line-height:58px;text-align:right;color:var(--white)}
</style>
</head>
<body>

<!-- Hero -->
<header class="hero">
  <div class="photo" style="left:0;top:0;width:1200px;height:676px;background:radial-gradient(ellipse at 62% 40%,rgba(120,110,100,.35),transparent 60%)" role="img" aria-label="Two consultants in suits in a bright modern office"></div>
  <div class="brand" style="left:97px;top:38px;font-size:22px"><span class="brand-mark"></span>Reach Crafters</div>
  <nav>
    <span class="nav" style="left:461px">HOME</span>
    <span class="nav" style="left:533px">ABOUT US</span>
    <span class="nav" style="left:634px">OUR SERVICES</span>
    <span class="nav" style="left:760px">OUR BLOG</span>
    <span class="nav" style="left:859px">CONTACT US</span>
  </nav>
  <span class="social" style="left:980px;top:47px;color:var(--white)"></span>
  <span class="social" style="left:1016px;top:47px;color:var(--white)"></span>
  <span class="social" style="left:1056px;top:47px;color:var(--white)"></span>
  <svg class="abs" style="left:1117px;top:48px" width="24" height="12" viewBox="0 0 24 12"><path d="M0 2h24M8 10h16" stroke="#fff" stroke-width="2"/></svg>
  <h1 class="hero-title">Be Found.<br>Be Chosen.</h1>
  <p class="hero-text">We aim to make the process easy for you!  We will find home health and take care of coordinating all care needed for your patient.</p>
  <a class="btn" style="left:162px;top:451px;width:137px;height:33px">Learn More</a>
  <span class="dot-ring" style="left:1109px;top:328px"></span>
  <span class="dot-ring" style="left:1109px;top:377px"></span>
  <svg class="abs" style="left:1120px;top:338px" width="12" height="60" viewBox="0 0 12 60"><path d="M3 8l3-4 3 4M3 53l3 4 3-4" stroke="#fff" fill="none" stroke-width="1.2"/></svg>
</header>

<!-- Who we are -->
<section>
  <h2 class="heading abs" style="left:162px;top:772px;font-size:58px">Who We Are</h2>
  <p class="sub abs" style="left:172px;top:850px">We Built trust in our <span style="color:var(--teal)">customer's mind..</span></p>
  <p class="who-text">Reach Crafters is a playbook-as-a-service consultancy that teaches high-ticket service businesses to understand why qualified buyers don't high-ticket service businesses to understand why qualified buyers don't choose them—and design buying experiences where reaching full commitment is the natural conclusion.<br>We apply the tools of Revenue Psychology and Revenue Intelligence to diagnose revenue problems and design solutions.</p>
  <a class="btn" style="left:610px;top:939px;width:137px;height:34px">Learn More</a>
</section>

<!-- How we help -->
<section>
  <div class="photo" style="left:547px;top:1086px;width:653px;height:417px;background:linear-gradient(120deg,#3b4656 0%,#6d7480 45%,#aeb4bc 70%,#4e5766 100%)" role="img" aria-label="Two businessmen reviewing a tablet together"></div>
  <svg class="abs" style="left:848px;top:1236px" width="114" height="114" viewBox="0 0 114 114"><circle cx="57" cy="57" r="57" fill="rgba(255,255,255,.35)"/><circle cx="57" cy="57" r="40" fill="#fff"/><path d="M50 44v26l21-13z" fill="var(--blue)"/></svg>
  <div class="help-panel">
    <h2 class="heading abs" style="left:162px;top:38px;font-size:36px;color:var(--white)">How We Help You Succeed</h2>
    <p class="sub abs" style="left:162px;top:94px;color:var(--white)">We are building great future Together, Be with us...</p>
    <div class="abs" style="left:160px;top:200px;width:1px;height:210px;border-left:1px dashed rgba(255,255,255,.6)"></div>
    <div class="step" style="top:177px;left:139px"><span class="step-num">1</span><span class="step-title">Strategic Frameworks</span><p class="step-text">Giving consultancy for every financial projection report and analysis for existing project.</p></div>
    <div class="step" style="top:282px;left:139px"><span class="step-num">2</span><span class="step-title">Data-Driven Insights</span><p class="step-text">Giving consultancy for every financial projection report and analysis for existing project.</p></div>
    <div class="step" style="top:388px;left:139px"><span class="step-num">3</span><span class="step-title">Growth Acceleration</span><p class="step-text">Giving consultancy for every financial projection report and analysis for existing project.</p></div>
  </div>
  <div class="abs" style="left:693px;top:1520px;font-family:'Poppins',sans-serif;font-style:italic;font-weight:600;font-size:72px;line-height:90px;color:var(--green)">10</div>
  <div class="abs" style="left:783px;top:1536px;font-family:'Playfair Display',serif;font-style:italic;font-size:21px;line-height:27px;color:var(--ink)">Years of<br>Experience</div>
</section>

<!-- Services -->
<section>
  <h2 class="heading abs center" style="top:1702px;font-size:38px">Our Services</h2>
  <p class="sub abs center" style="top:1760px">We are building great future Together, Be with us</p>
  <div class="service" style="left:93px">
    <div class="service-img" style="background:linear-gradient(160deg,#e9ecef,#c7cdd4 55%,#5d6a7c)" role="img" aria-label="Consultant guiding a colleague at a laptop"></div>
    <svg class="service-arrow" width="28" height="14" viewBox="0 0 28 14"><path d="M0 7h26M20 1l6 6-6 6" stroke="#222" fill="none" stroke-width="1.5"/></svg>
    <span class="service-cat">BUSINESS</span><span class="service-name">Revenue Intelligence</span><span class="service-line"></span>
  </div>
  <div class="service" style="left:440px">
    <div class="service-img" style="background:linear-gradient(160deg,#dfe3e8,#9aa4b1 50%,#2f3b52)" role="img" aria-label="Two colleagues reviewing a phone together"></div>
    <svg class="service-arrow" width="28" height="14" viewBox="0 0 28 14"><path d="M0 7h26M20 1l6 6-6 6" stroke="#222" fill="none" stroke-width="1.5"/></svg>
    <span class="service-cat">BUSINESS</span><span class="service-name">Revenue Psychology</span><span class="service-line"></span>
  </div>
  <div class="service" style="left:785px">
    <div class="service-img" style="background:linear-gradient(160deg,#e4e8ec,#aab2bc 50%,#3c4658)" role="img" aria-label="Businessmen in discussion at a meeting table"></div>
    <svg class="service-arrow" width="28" height="14" viewBox="0 0 28 14"><path d="M0 7h26M20 1l6 6-6 6" stroke="#222" fill="none" stroke-width="1.5"/></svg>
    <span class="service-cat">BUSINESS</span><span class="service-name">Demand Architecture</span><span class="service-line"></span>
  </div>
  <a class="btn" style="left:516px;top:2381px;width:168px;height:35px">View All Services</a>
</section>

<!-- Testimonials -->
<section>
  <h2 class="heading abs center" style="top:2490px;font-size:38px">Client Testimonial</h2>
  <p class="sub abs center" style="top:2548px">We are building great future Together, Be with us</p>
  <div class="photo" style="left:162px;top:2612px;width:276px;height:264px;background:linear-gradient(150deg,#7d8590,#4b535e 55%,#2c3138)" role="img" aria-label="Portrait of a senior male consultant"></div>
  <div class="quote-panel" style="left:438px;top:2640px;width:600px;height:210px">
    <span class="quote-name" style="left:36px;top:36px">GRANT HOLLIS</span>
    <span class="quote-role" style="left:38px;top:68px">Founder and Principal Regulatory Affairs Consultant</span>
    <p class="quote-text" style="left:38px;top:98px">Grant has a doctorate in cancer research and more than 20 years of experience in the pharmaceutical and biotechnology industries. During his career, he has led EU, US, and UK regulatory projects in industry and consulting.</p>
  </div>
  <div class="quote-panel" style="left:162px;top:2951px;width:600px;height:209px">
    <span class="quote-name" style="left:36px;top:36px">NORA WHITFIELD</span>
    <span class="quote-role" style="left:38px;top:68px">Expert Regulatory Affairs Consultant</span>
    <p class="quote-text" style="left:38px;top:98px">Nora has a doctorate in cancer research and more than 20 years of experience in the pharmaceutical and biotechnology industries. During her career, she has led EU, US, and UK regulatory projects in industry and consulting.</p>
  </div>
  <div class="photo" style="left:762px;top:2924px;width:276px;height:263px;background:linear-gradient(150deg,#b8a98a,#d9c9a6 45%,#8a7c66)" role="img" aria-label="Portrait of a smiling female consultant"></div>
</section>

<!-- Blog -->
<section>
  <h2 class="heading abs center" style="top:3262px;font-size:38px">Latest Blog</h2>
  <p class="sub abs center" style="top:3320px">We are building great future Together, Be with us</p>
  <article class="post" style="left:162px">
    <div class="post-img" style="background:linear-gradient(150deg,#dfe3e7,#8e99a8 55%,#2d3a55)" role="img" aria-label="Two businessmen reviewing documents at a desk"></div>
    <h3 class="post-title">7 Tips to Improve your Mental Health in 2024</h3>
    <p class="post-excerpt">Consectetuer fringilla aenean sagittis potenti ullamcorper nam porta feugiat</p>
    <div class="post-rule"></div>
    <p class="post-author">Virtual Assistant</p><p class="post-date">Jan 02, 2026</p>
  </article>
  <article class="post" style="left:463px">
    <div class="post-img" style="background:linear-gradient(150deg,#c9ced4,#6d7580 55%,#262b33)" role="img" aria-label="Two men in suits in an office conversation"></div>
    <h3 class="post-title">PTSD: Causes, Symptoms, &amp; When to Seek Treatment</h3>
    <p class="post-excerpt">Consectetuer fringilla aenean sagittis potenti ullamcorper nam porta feugiat</p>
    <div class="post-rule"></div>
    <p class="post-author">Virtual Assistant</p><p class="post-date">Jan 02, 2026</p>
  </article>
  <article class="post" style="left:762px">
    <div class="post-img" style="background:linear-gradient(150deg,#b9bec5,#5f6772 55%,#24282f)" role="img" aria-label="Businessmen looking at a tablet together"></div>
    <h3 class="post-title">Is counselling free in Manitoba?</h3>
    <p class="post-excerpt">Consectetuer fringilla aenean sagittis potenti ullamcorper nam porta feugiat</p>
    <div class="post-rule"></div>
    <p class="post-author">Virtual Assistant</p><p class="post-date">Jan 02, 2026</p>
  </article>
  <a class="btn" style="left:516px;top:3797px;width:168px;height:36px">View All Blog</a>
</section>

<!-- Contact -->
<section>
  <div class="photo" style="left:23px;top:3976px;width:331px;height:510px;background:linear-gradient(170deg,#2f5fae 0%,#5b87c9 40%,#8d8f94 70%,#5a5c5f 100%)" role="img" aria-label="Modern angular building against a blue sky"></div>
  <div class="photo" style="left:846px;top:3976px;width:331px;height:510px;background:linear-gradient(190deg,#2f5fae 0%,#5b87c9 40%,#8d8f94 70%,#5a5c5f 100%)" role="img" aria-label="Modern angular building against a blue sky"></div>
  <div class="contact-card">
    <p class="abs" style="left:0;width:492px;top:50px;text-align:center;font-size:12px;color:var(--blue)">Contact</p>
    <h2 class="heading abs" style="left:0;width:492px;top:68px;text-align:center;font-size:32px">Get In Touch</h2>
    <span class="field" style="left:50px;top:146px;width:178px">Name*</span>
    <span class="field" style="left:266px;top:146px;width:178px">Company Name</span>
    <span class="field" style="left:50px;top:207px;width:178px">Phone</span>
    <span class="field" style="left:266px;top:207px;width:178px">Email Address*</span>
    <span class="field" style="left:50px;top:269px;width:394px">State</span>
    <span class="field" style="left:50px;top:331px;width:394px;height:70px">Your Message</span>
    <div class="captcha">
      <span class="abs" style="left:10px;top:19px;width:20px;height:20px;border:2px solid #c1c1c1;background:#fff;border-radius:2px"></span>
      <span class="abs" style="left:40px;top:22px;font-size:9px;color:#222">I'm not a robot</span>
      <span class="abs" style="left:184px;top:14px;width:22px;height:22px;border-radius:50%;background:#9aa5b8"></span>
      <span class="abs" style="left:176px;top:40px;font-size:6px;color:#777">Privacy · Terms</span>
    </div>
    <a class="btn" style="left:193px;top:497px;width:106px;height:35px;font-size:12px;font-weight:500">SUBMIT</a>
  </div>
</section>

<!-- Footer -->
<footer class="footer">
  <div class="brand" style="left:162px;top:124px;font-size:22px"><span class="brand-mark"></span>Reach Crafters</div>
  <h4 class="foot-head" style="left:430px;top:52px">Quick Links</h4>
  <ul class="foot-list" style="left:430px;top:76px"><li>Home</li><li>About Us</li><li>Our Services</li><li>Our Blog</li><li>Contact Us</li></ul>
  <h4 class="foot-head" style="left:610px;top:52px">Services</h4>
  <ul class="foot-list" style="left:610px;top:76px"><li>Revenue Intelligence</li><li>Revenue Psychology</li><li>Demand Architecture</li><li>Advisory</li></ul>
  <h4 class="foot-head" style="left:819px;top:52px">Contact Us</h4>
  <svg class="abs" style="left:824px;top:90px" width="12" height="12" viewBox="0 0 24 24"><path d="M6.6 10.8a15 15 0 006.6 6.6l2.2-2.2a1 1 0 011-.25 11.4 11.4 0 003.6.57 1 1 0 011 1V20a1 1 0 01-1 1A17 17 0 013 4a1 1 0 011-1h3.5a1 1 0 011 1c0 1.25.2 2.45.57 3.57a1 1 0 01-.25 1z" fill="#fff"/></svg>
  <span class="foot-small" style="left:852px;top:88px">555-014-2290</span>
  <svg class="abs" style="left:824px;top:118px" width="13" height="10" viewBox="0 0 26 20"><rect width="26" height="20" rx="2" fill="#fff"/><path d="M1 2l12 9 12-9" stroke="#232427" stroke-width="2" fill="none"/></svg>
  <span class="foot-small" style="left:852px;top:115px">hello@reachcrafters-mail.com</span>
  <div class="abs" style="left:819px;top:152px;width:220px;height:1px;background:#55575c"></div>
  <span class="social" style="left:824px;top:172px;color:var(--white)"></span>
  <span class="social" style="left:867px;top:172px;color:var(--white)"></span>
  <span class="social" style="left:908px;top:172px;color:var(--white)"></span>
  <span class="foot-small" style="left:162px;top:320px">2026 Consulting. All Right Reserved.</span>
  <span class="foot-small" style="left:162px;top:343px">Terms &amp; Conditions &nbsp;&nbsp; - &nbsp;&nbsp; Privacy Policy</span>
  <div class="cta">Get In<br>Touch <svg width="40" height="40" viewBox="0 0 40 40" style="vertical-align:-2px"><path d="M4 36L36 4M14 4h22v22" stroke="#fff" stroke-width="2.5" fill="none"/></svg></div>
</footer>

</body>
</html>
```